Vigil Ledger Suite (Web Design)

Design with your logo. Background in black or dark. Elegant style, it's a website for professional people only. Our company provides a cloud software manager for Funeral Services Companies.

Target Market(s)

Professional of Funeral Services.

Coding

Coded - Design and coding required

Number of Pages Required

3 page

Font styles to use
Sans Serif

Colors
fbee3d
000000
5c5c5c

Requirements
Must have
• Design of the website should be similar to our logo colors.

```html
<!DOCTYPE html>
<html lang="en">
<head>
<meta charset="utf-8">
<title>Vigil Ledger Suite</title>
<link href="https://fonts.googleapis.com/css2?family=Montserrat:wght@400;500;600;700&family=Open+Sans:wght@400;600&display=swap" rel="stylesheet">
<style>
:root{
  --yellow:#fbee3d;
  --gold:#f2c200;
  --black:#000000;
  --ink:#111111;
  --dark:#1c1c1c;
  --grey:#5c5c5c;
  --light:#f4f4f4;
  --sky:#a8d8ea;
  --line:#cfcfcf;
  --white:#ffffff;
}
*{margin:0;padding:0;box-sizing:border-box}
html,body{width:1200px;height:3243px;overflow:hidden}
body{position:relative;background:var(--white);font-family:"Open Sans",Arial,sans-serif;color:var(--grey)}
.abs{position:absolute}
.center{text-align:center}

/* header */
.topline{left:0;top:0;width:1200px;height:5px;background:var(--gold)}
.brand{left:112px;top:44px;display:flex;align-items:center;gap:12px}
.brand-dot{width:26px;height:26px;border-radius:50%;background:var(--gold)}
.brand-name{font-family:"Montserrat",sans-serif;font-weight:700;font-size:26px;color:var(--gold);letter-spacing:1px;white-space:nowrap}
.nav{top:66px;font-family:"Montserrat",sans-serif;font-size:14px;font-weight:500;color:var(--ink);letter-spacing:.5px}
.nav.active{color:var(--gold)}

/* hero */
.hero{left:0;top:140px;width:1200px;height:653px;clip-path:polygon(0 0,100% 0,100% 515px,0 653px);
  background:radial-gradient(ellipse at 50% 45%,#1f5f66 0%,#0d2a33 30%,#050a10 65%,#000 100%)}
.hero-title{left:324px;top:339px;width:552px;height:63px;background:#c8b400;display:flex;align-items:center;justify-content:center;
  font-family:"Montserrat",sans-serif;font-weight:700;font-size:34px;color:var(--white);letter-spacing:1px}
.hero-sub{left:0;top:437px;width:1200px;font-family:"Montserrat",sans-serif;font-weight:600;font-size:17px;color:var(--white);letter-spacing:.6px}
.arrow{width:36px;height:36px;border-radius:50%;border:2px solid var(--white);display:flex;align-items:center;justify-content:center}

/* section heads */
.sec-title{left:0;width:1200px;font-family:"Montserrat",sans-serif;font-weight:600;font-size:34px;color:var(--gold)}
.sec-sub{left:0;width:1200px;font-size:13px;color:var(--grey)}

/* services */
.service{width:320px;text-align:center}
.service .ring{width:116px;height:116px;border-radius:50%;border:2px solid #3a3a3a;margin:0 auto;display:flex;align-items:center;justify-content:center}
.service h3{font-family:"Montserrat",sans-serif;font-weight:500;font-size:17px;color:var(--ink);letter-spacing:.5px;margin-top:30px}
.service p{font-size:13px;line-height:27px;margin-top:8px;color:var(--grey)}

/* welcome */
.welcome{left:0;top:1479px;width:605px;height:499px;background:var(--dark)}
.welcome h2{position:absolute;left:112px;top:38px;font-family:"Montserrat",sans-serif;font-weight:600;font-size:30px;line-height:44px;color:var(--gold);letter-spacing:.5px}
.welcome p{position:absolute;left:112px;width:445px;font-size:12px;line-height:26px;color:#8a8a8a}
.btn-solid{position:absolute;left:112px;top:402px;width:225px;height:50px;background:var(--gold);color:var(--ink);
  font-family:"Montserrat",sans-serif;font-size:13px;font-weight:600;display:flex;align-items:center;justify-content:center}
.welcome-art{left:605px;top:1479px;width:595px;height:499px;background:linear-gradient(160deg,#b7e1ef 0%,#9fd2e6 100%)}

/* blog */
.post{top:2166px;width:305px}
.post .photo{width:305px;height:216px;background:linear-gradient(135deg,#6c7480,#2f3640)}
.post .date{position:absolute;left:14px;top:16px;width:44px;height:54px;background:var(--gold);text-align:center;font-family:"Montserrat",sans-serif;color:var(--ink)}
.post .date b{display:block;font-size:22px;line-height:30px;font-weight:600}
.post .date span{font-size:11px}
.post .card{position:absolute;left:18px;top:180px;width:270px;height:162px;background:var(--white);border:1px solid var(--line);border-top:none;padding:18px 16px 0}
.post h4{font-family:"Montserrat",sans-serif;font-size:11px;font-weight:700;color:var(--ink);white-space:nowrap}
.post .card p{font-size:12px;line-height:24px;margin-top:10px;color:var(--grey)}
.btn-outline{position:absolute;left:76px;top:140px;width:118px;height:36px;background:var(--white);border:1px solid var(--line);
  color:var(--gold);font-family:"Montserrat",sans-serif;font-size:14px;font-weight:500;display:flex;align-items:center;justify-content:center}

/* testimonials */
.testi-band{left:0;top:2573px;width:1200px;height:264px;background:var(--light)}
.avatar{width:130px;height:130px;border-radius:50%;border:4px solid var(--white);background:linear-gradient(160deg,#c7a48e,#6f5a4f)}
.quote{width:310px;font-size:12px;line-height:24px;color:var(--grey);border-left:1px solid var(--line);padding-left:20px}
.quote .mark{font-family:"Montserrat",sans-serif;font-size:26px;font-weight:700;color:var(--gold);line-height:10px;vertical-align:-6px;margin-right:4px}
.person{font-size:12px;color:var(--grey)}
.stars{display:flex;gap:3px}

/* footer */
.footer{left:0;top:2837px;width:1200px;height:406px;background:#111}
.foot-brand{left:130px;top:2985px;display:flex;align-items:center;gap:12px}
.foot-brand .brand-dot{width:28px;height:28px}
.foot-brand .brand-name{font-size:24px}
.foot-head{top:2872px;font-family:"Montserrat",sans-serif;font-size:27px;font-weight:500;color:var(--white)}
.foot-info{left:493px;top:2932px;font-size:13px;line-height:19px;color:var(--white)}
.foot-info dt{margin-top:15px}
.foot-info dt:first-child{margin-top:0}
.field{left:744px;width:283px;height:37px;background:var(--white);font-size:11px;color:#666;padding:10px 12px}
.submit{left:744px;top:3105px;width:88px;height:32px;background:var(--gold);color:var(--white);font-family:"Montserrat",sans-serif;font-size:12px;font-weight:700;display:flex;align-items:center;justify-content:center}
.foot-rule{left:112px;top:3161px;width:976px;height:1px;background:#2a2a2a}
.copy{left:0;top:3190px;width:1200px;font-size:13px;color:var(--white)}
</style>
</head>
<body>

<header>
  <div class="abs topline"></div>
  <div class="abs brand"><span class="brand-dot"></span><span class="brand-name">VIGIL LEDGER SUITE</span></div>
  <nav>
    <span class="abs nav active" style="left:500px">HOME</span>
    <span class="abs nav" style="left:604px">PRESENTATION</span>
    <span class="abs nav" style="left:772px">SERVICES</span>
    <span class="abs nav" style="left:900px">GALLERY</span>
    <span class="abs nav" style="left:1023px">CONTACT</span>
  </nav>
</header>

<section>
  <div class="abs hero" role="img" aria-label="Open hand beneath a glowing network of data points and binary digits"></div>
  <div class="abs hero-title">VIGIL LEDGER SUITE</div>
  <div class="abs hero-sub center">SED UT PERSPICIATIS UNDE OMNIS ISTE NATUS ERROR SIT VOLUPTATEM ACCUSANTIUM</div>
  <div class="abs arrow" style="left:58px;top:449px"><svg width="12" height="14" viewBox="0 0 12 14"><path d="M8 2 L3 7 L8 12" fill="none" stroke="#fff" stroke-width="2"/></svg></div>
  <div class="abs arrow" style="left:1095px;top:449px"><svg width="12" height="14" viewBox="0 0 12 14"><path d="M4 2 L9 7 L4 12" fill="none" stroke="#fff" stroke-width="2"/></svg></div>
</section>

<section>
  <h2 class="abs sec-title center" style="top:788px">OUR SERVICES</h2>
  <p class="abs sec-sub center" style="top:867px">Sed ut perspiciatis unde omnis iste natus error sit voluptatem accusantium doloremque laudantium, totam rem</p>

  <div class="abs service" style="left:110px;top:941px">
    <div class="ring"><svg width="56" height="56" viewBox="0 0 56 56" fill="none" stroke="#f2c200" stroke-width="2"><rect x="8" y="10" width="40" height="28" rx="2"/><path d="M22 46h12M28 38v8"/><circle cx="28" cy="24" r="7"/><circle cx="28" cy="24" r="2"/></svg></div>
    <h3>ONLINE SOFTWARE</h3>
    <p>Sed ut perspiciatis unde omnis iste natus error<br>accusantium doloremque</p>
  </div>
  <div class="abs service" style="left:439px;top:941px">
    <div class="ring"><svg width="56" height="56" viewBox="0 0 56 56" fill="none" stroke="#f2c200" stroke-width="2"><path d="M12 14h22l8 8v26H12z"/><path d="M18 8h22l8 8v26"/><path d="M18 28h18M18 34h18M18 40h12"/></svg></div>
    <h3>PERSONALIZED DOCUMENTS</h3>
    <p>Sed ut perspiciatis unde omnis iste natus error<br>accusantium doloremque</p>
  </div>
  <div class="abs service" style="left:774px;top:941px">
    <div class="ring"><svg width="56" height="56" viewBox="0 0 56 56" fill="none" stroke="#f2c200" stroke-width="2"><rect x="12" y="8" width="22" height="40" rx="2"/><circle cx="34" cy="32" r="12"/><circle cx="34" cy="32" r="4"/></svg></div>
    <h3>SOFTWARE CUSTOMIZATION</h3>
    <p>Sed ut perspiciatis unde omnis iste natus error<br>accusantium doloremque</p>
  </div>

  <div class="abs service" style="left:110px;top:1209px">
    <div class="ring"><svg width="56" height="56" viewBox="0 0 56 56" fill="none" stroke="#f2c200" stroke-width="2"><rect x="16" y="6" width="24" height="44" rx="2"/><rect x="20" y="11" width="16" height="8"/><path d="M21 25h4M27 25h4M33 25h2M21 31h4M27 31h4M33 31h2M21 37h4M27 37h4M33 37h2M21 43h14"/></svg></div>
    <h3>BILLING</h3>
    <p>Sed ut perspiciatis unde omnis iste natus error<br>accusantium doloremque</p>
  </div>
  <div class="abs service" style="left:439px;top:1209px">
    <div class="ring"><svg width="56" height="56" viewBox="0 0 56 56" fill="none" stroke="#f2c200" stroke-width="2"><path d="M16 40V26a12 12 0 0 1 24 0v14l4 4H12z"/><path d="M24 48a4 4 0 0 0 8 0M28 10v4"/></svg></div>
    <h3>NOTIFICATIONS</h3>
    <p>Sed ut perspiciatis unde omnis iste natus error<br>accusantium doloremque</p>
  </div>
  <div class="abs service" style="left:774px;top:1209px">
    <div class="ring"><svg width="56" height="56" viewBox="0 0 56 56" fill="none" stroke="#f2c200" stroke-width="2"><rect x="16" y="6" width="24" height="44" rx="3"/><path d="M16 12h24M16 42h24"/><circle cx="28" cy="27" r="4"/><path d="M28 19v3M28 32v3M20 27h3M33 27h3"/></svg></div>
    <h3>DISPLAY ON SCREENS</h3>
    <p>Sed ut perspiciatis unde omnis iste natus error<br>accusantium doloremque</p>
  </div>
</section>

<section>
  <div class="abs welcome">
    <h2>WELCOME TO<br>VIGIL LEDGER SUITE</h2>
    <p style="top:144px">Sed ut perspiciatis unde omnis iste natus error sit voluptatem accusantium doloremque laudantium, totam rem aperiam, eaque ipsa quae ab illo inventore veritatis et quasi architecto beatae vitae dicta sunt explicabo. Nemo enim ipsam voluptatem quia voluptas sit aspernatur aut odit aut fugit, sed quia consequuntur magni dolores eos qui ratione voluptatem sequi nesciunt.</p>
    <p style="top:296px">Neque porro quisquam est, qui dolorem ipsum quia dolor sit amet, consectetur, adipisci velit, sed quia non numquam eius modi tempora incidunt ut labore et dolore magnam aliquam quaerat voluptatem.</p>
    <div class="btn-solid">CLICK HERE FOR MORE INFO</div>
  </div>
  <div class="abs welcome-art" role="img" aria-label="Illustration of gears, a software disc, a document and a monitor with a cloud download and a video play button"></div>
</section>

<section>
  <h2 class="abs sec-title center" style="top:2031px">LATEST BLOG</h2>
  <p class="abs sec-sub center" style="top:2112px">Sed ut perspiciatis unde omnis iste natus error sit voluptatem accusantium doloremque laudantium, totam rem</p>

  <article class="abs post" style="left:112px">
    <div class="photo" role="img" aria-label="Hands typing on a laptop showing a cloud screen"></div>
    <div class="date"><b>02</b><span>JAN</span></div>
    <div class="card"><h4>SED UT PERSPICIATIS UNDE OMNIS</h4><p>Sed ut perspiciatis unde omnis iste natus err or sit voluptatem accusantium dolorem vitae dicta sunt explicabo.</p><div class="btn-outline">READ MORE</div></div>
  </article>
  <article class="abs post" style="left:447px">
    <div class="photo" role="img" aria-label="Businessman holding a tablet with cloud network graphics" style="background:linear-gradient(135deg,#1d3b58,#0a1622)"></div>
    <div class="date"><b>02</b><span>JAN</span></div>
    <div class="card"><h4>SED UT PERSPICIATIS UNDE OMNIS</h4><p>Sed ut perspiciatis unde omnis iste natus err or sit voluptatem accusantium dolorem vitae dicta sunt explicabo.</p><div class="btn-outline">READ MORE</div></div>
  </article>
  <article class="abs post" style="left:783px">
    <div class="photo" role="img" aria-label="Office desk with documents and charts" style="background:linear-gradient(135deg,#8b7a5e,#3e3426)"></div>
    <div class="date"><b>02</b><span>JAN</span></div>
    <div class="card"><h4>SED UT PERSPICIATIS UNDE OMNIS</h4><p>Sed ut perspiciatis unde omnis iste natus err or sit voluptatem accusantium dolorem vitae dicta sunt explicabo.</p><div class="btn-outline">READ MORE</div></div>
  </article>
</section>

<section>
  <div class="abs testi-band"></div>
  <div class="abs avatar" style="left:117px;top:2631px" role="img" aria-label="Portrait of a smiling client"></div>
  <div class="abs quote" style="left:266px;top:2630px"><span class="mark">“</span>Sed ut perspiciatis unde omnis iste natus error sit voluptatem accusantium doloremque laudantium, totam rem aperiam, eaque ipsa quae ab illo inventore veritatis et quasi architecto beatae vitae dicta sunt explicabo.</div>
  <div class="abs person" style="left:288px;top:2772px">- MARC DELORME</div>
  <div class="abs stars" style="left:513px;top:2774px">
    <svg width="60" height="12" viewBox="0 0 60 12"><g fill="#f2c200"><path id="st" d="M6 0l1.8 3.8 4.2.5-3.1 2.9.8 4.2L6 9.3 2.3 11.4l.8-4.2L0 4.3l4.2-.5z"/><use href="#st" x="12"/><use href="#st" x="24"/></g><g fill="#777"><use href="#st" x="36"/><use href="#st" x="48"/></g></svg>
  </div>

  <div class="abs avatar" style="left:623px;top:2631px;background:linear-gradient(160deg,#d2b39c,#7a6453)" role="img" aria-label="Portrait of a smiling client with glasses"></div>
  <div class="abs quote" style="left:772px;top:2630px"><span class="mark">“</span>Sed ut perspiciatis unde omnis iste natus error sit voluptatem accusantium doloremque laudantium, totam rem aperiam, eaque ipsa quae ab illo inventore veritatis et quasi architecto beatae vitae dicta sunt explicabo.</div>
  <div class="abs person" style="left:794px;top:2772px">- MARC DELORME</div>
  <div class="abs stars" style="left:1019px;top:2774px">
    <svg width="60" height="12" viewBox="0 0 60 12"><g fill="#f2c200"><use href="#st"/><use href="#st" x="12"/><use href="#st" x="24"/></g><g fill="#777"><use href="#st" x="36"/><use href="#st" x="48"/></g></svg>
  </div>
</section>

<footer>
  <div class="abs footer"></div>
  <div class="abs foot-brand"><span class="brand-dot"></span><span class="brand-name">VIGIL LEDGER SUITE</span></div>

  <h3 class="abs foot-head" style="left:493px">ADDRESS</h3>
  <dl class="abs foot-info">
    <dt>ADDRESS</dt><dd># 245 &nbsp;Lorem Ipsum DUmmy<br>Lorem Ipsum</dd>
    <dt>PHONE</dt><dd>(000)-555-0148</dd>
    <dt>EMAIL</dt><dd>hello@vigilledger.example</dd>
  </dl>

  <h3 class="abs foot-head" style="left:746px">CONTACT FORM</h3>
  <div class="abs field" style="top:2925px">Name :</div>
  <div class="abs field" style="top:2966px">Email :</div>
  <div class="abs field" style="top:3006px">Subject :</div>
  <div class="abs field" style="top:3046px;height:48px">Message :</div>
  <div class="abs submit">SUBMIT</div>

  <div class="abs foot-rule"></div>
  <p class="abs copy center">© Copyright 2019 Vigil Ledger Suite.All right reserved</p>
</footer>

</body>
</html>
```